Business Card Design Project for a Restaurant/Wine Bar

New, fresh business card design for Brevenna Wine Bar & Restaurant, Bandon, Oregon. We are an established restaurant on the Oregon coast featuring "Italian coastal cuisine."

"Brevenna" means bay leaf in Italian. We aren't sure if we would like our logo on the card or not, but if you have something interesting that uses it, then please do so. The basic information is essential - full restaurant name, address, phone and website (do not use www). The font on our menu and wine list may give you some sort of an idea of our style.

One-sided card needed as we often use the backside to write down various types of info for customers.
Updates

After seeing a few submissions, we would like to see what designers can come up with-using the logo, just the leaf, or none at all. Sky is the limit as long as our full restaurant name, address, phone and website (please leave out www) are there. Please contact us if questions!

I appreciate all of your designs! Our deadline is next week, but I will continue to give feedback on designs as I can. This is our busiest season, so my co-owner/chef/husband, won't have time to look at the designs for awhile. When he does, we can make our decision.

cheers,
Maren

Target Market(s)

Fine dining/wine crowd. Would like something simple and elegant, but not pretentious or stuffy. Brevenna means bay laurel (bay leaf) in Italian (please see our logo).

Industry/Entity Type

Restaurant

Requirements
Must have
• Full Name of Restaurant: Brevenna Wine Bar & Restaurant
Address: 812 4th Ave NW, Bandon, Oregon 97411
Phone: 541.555.0172
website: brevennawinebar.example (do not use www)
Should not have
• Loud colors.

```html
<!DOCTYPE html>
<html lang="en">
<head>
<meta charset="utf-8">
<title>Brevenna Wine Bar &amp; Restaurant — Business Card</title>
<link rel="stylesheet" href="https://fonts.googleapis.com/css2?family=Tinos&family=PT+Sans&display=swap">
<style>
  :root {
    --backdrop: #6e4a2e;
    --card: #ffffff;
    --card-shade: #e9e9ea;
    --ink: #1a1a1a;
    --navy: #2a3488;
    --body: #3a3a3a;
    --rule: #bdbdbd;
    --ghost: #dcdcdc;
  }
  * { box-sizing: border-box; margin: 0; padding: 0; }
  html, body { width: 1200px; height: 966px; overflow: hidden; }
  body {
    background: var(--backdrop);
    position: relative;
    font-family: "PT Sans", sans-serif;
  }
  .card {
    position: absolute;
    width: 640px;
    height: 380px;
    border-radius: 26px;
    box-shadow: 0 8px 22px rgba(0,0,0,0.35);
  }
  .card-front {
    left: 80px; top: 90px;
    background: linear-gradient(115deg, var(--card-shade) 0%, var(--card) 45%, var(--card-shade) 100%);
  }
  .card-back {
    left: 480px; top: 496px;
    background: var(--card);
    overflow: hidden;
  }
  .brand-mark {
    position: absolute;
    left: 64px; top: 46px;
    font-family: "Tinos", serif;
    font-size: 70px;
    color: var(--ink);
    letter-spacing: 1px;
  }
  .restaurant-name {
    position: absolute;
    left: 64px; top: 228px;
    font-family: "Tinos", serif;
    font-size: 35px;
    color: var(--navy);
  }
  .contact-line {
    position: absolute;
    left: 56px; top: 296px;
    display: flex; align-items: center; gap: 18px;
    font-size: 17px; color: var(--body);
  }
  .contact-item { display: flex; align-items: center; gap: 4px; }
  .contact-item svg { width: 16px; height: 16px; }
  .address {
    position: absolute;
    left: 56px; top: 328px;
    font-size: 17px; color: var(--body);
  }
  .note-lines {
    position: absolute;
    left: 60px; right: 40px; top: 48px;
    display: flex; flex-direction: column; gap: 40px;
  }
  .note-line { height: 1px; background: var(--rule); }
  .ghost-name {
    position: absolute;
    left: 0; right: 0; top: 150px;
    text-align: center;
    font-family: "Tinos", serif;
    font-size: 74px;
    color: var(--ghost);
  }
</style>
</head>
<body>
  <section class="card card-front" aria-label="Card front">
    <div class="brand-mark">Brevenna</div>
    <h1 class="restaurant-name">Brevenna Wine Bar &amp; Restaurant</h1>
    <div class="contact-line">
      <span class="contact-item">
        <svg viewBox="0 0 16 16" aria-hidden="true"><circle cx="8" cy="8" r="7" fill="none" stroke="#2a3488" stroke-width="1.3"/><path d="M5.5 4.5c-.8 2.6.9 5.9 3.9 7l1.2-1.4-1.6-1.2-.8.7c-1-.6-1.6-1.5-1.9-2.6l.9-.6-.8-1.9z" fill="#2a3488"/></svg>
        541.555.0172
      </span>
      <span class="contact-item">
        <svg viewBox="0 0 16 16" aria-hidden="true"><g fill="none" stroke="#2a3488" stroke-width="1.2"><circle cx="8" cy="8" r="7"/><ellipse cx="8" cy="8" rx="3" ry="7"/><path d="M1 8h14M2.5 4.5h11M2.5 11.5h11"/></g></svg>
        brevennawinebar.example
      </span>
    </div>
    <p class="address">812 4th Ave NW, Bandon, Oregon 97411</p>
  </section>

  <section class="card card-back" aria-label="Card back for handwritten notes">
    <div class="ghost-name">Brevenna</div>
    <div class="note-lines">
      <div class="note-line"></div>
      <div class="note-line"></div>
      <div class="note-line"></div>
      <div class="note-line"></div>
      <div class="note-line"></div>
      <div class="note-line"></div>
      <div class="note-line"></div>
    </div>
  </section>
</body>
</html>
```